Private Investigation Business Card Design

I need a business card for a new private investigation company named Brisk Inquiries. I perform mainly surveillance jobs, vehicle repossessions, document serves etc. The final design should aim for a professional look. The logo has a magnifying glass with stick man arms and legs and is in a running action to show the "Brisk" aspect of the name. If the colour scheme could remain the same as the website www.briskinquiries-demo.com.au with silvers,blacks and a couple electric blue highlights.
Industry/Entity Type
Business
Contact Information for Business Card
Morgan Kellaway
Brisk Inquiries
0487316204
PO Box 58, Carnwell NSW 2291
info@briskinquiries-demo.com.au
www.briskinquiries-demo.com.au
Look and feel

```html
<!DOCTYPE html>
<html lang="en">
<head>
<meta charset="utf-8">
<title>Brisk Inquiries – Business Card</title>
<link rel="stylesheet" href="https://fonts.googleapis.com/css2?family=Open+Sans:wght@400;600;700&display=swap">
<style>
  :root {
    --stage: #3a3532;
    --silver-light: #e4e4e6;
    --silver-mid: #c9c9cc;
    --silver-dark: #a9a9ad;
    --ink: #1d1d1f;
    --ink-soft: #3a3a3d;
    --edge: #8d8d92;
  }
  * { box-sizing: border-box; margin: 0; padding: 0; }
  html, body {
    width: 1200px; height: 844px; overflow: hidden;
    background: var(--stage);
    font-family: "Open Sans", Arial, sans-serif;
  }
  .canvas {
    position: relative; width: 1200px; height: 844px;
    display: flex; align-items: center; justify-content: center; gap: 56px;
  }
  .card {
    position: relative; width: 500px; height: 286px;
    background: linear-gradient(160deg, var(--silver-light) 0%, var(--silver-mid) 55%, var(--silver-dark) 100%);
    border: 1px solid var(--edge);
    box-shadow: 0 10px 24px rgba(0,0,0,.45);
    color: var(--ink);
  }
  .brand {
    position: absolute; display: flex; align-items: center; gap: 10px;
    font-weight: 700; color: var(--ink-soft); letter-spacing: 1px;
    text-transform: uppercase; white-space: nowrap;
  }
  .brand-dot {
    width: 14px; height: 14px; border-radius: 50%;
    background: var(--ink-soft); flex: none;
  }
  .card-front .brand { top: 40px; right: 48px; font-size: 30px; }
  .card-back .brand { top: 50%; left: 50%; transform: translate(-50%, -50%); font-size: 40px; }
  .contact {
    position: absolute; left: 34px; top: 122px;
    font-size: 13px; line-height: 17px; color: var(--ink);
  }
  .contact-name { font-size: 16px; font-weight: 700; line-height: 19px; }
  .contact-company { margin-bottom: 12px; }
  .contact-address { margin-bottom: 8px; }
  .contact-line { display: flex; align-items: center; gap: 8px; }
  .contact-line svg { width: 11px; height: 11px; fill: var(--ink); flex: none; }
</style>
</head>
<body>
<main class="canvas">
  <section class="card card-front" aria-label="Card front">
    <div class="brand"><span class="brand-dot"></span>Brisk Inquiries</div>
    <div class="contact">
      <p class="contact-name">Morgan Kellaway</p>
      <p class="contact-company">Brisk Inquiries</p>
      <p class="contact-address">PO Box 58, Carnwell<br>NSW 2291</p>
      <p class="contact-line">
        <svg viewBox="0 0 12 12" aria-hidden="true"><path d="M2.5 1h2l1 3-1.3 1a6 6 0 0 0 2.8 2.8L8 6.5l3 1v2a1.5 1.5 0 0 1-1.5 1.5A8.5 8.5 0 0 1 1 2.5 1.5 1.5 0 0 1 2.5 1z"/></svg>
        0487316204
      </p>
      <p class="contact-line">
        <svg viewBox="0 0 12 12" aria-hidden="true"><path d="M1 2.5h10v7H1z M1.5 3l4.5 3.5L10.5 3" stroke="#e4e4e6" stroke-width=".8"/></svg>
        info@briskinquiries-demo.com.au
      </p>
      <p class="contact-line">
        <svg viewBox="0 0 12 12" aria-hidden="true"><path d="M4.5 7.5l3-3" stroke="#1d1d1f" stroke-width="1.3" fill="none"/><path d="M5 3.5l1.5-1.5a2 2 0 0 1 3 3L8 6.5M7 8.5l-1.5 1.5a2 2 0 0 1-3-3L4 5.5" stroke="#1d1d1f" stroke-width="1.3" fill="none"/></svg>
        www.briskinquiries-demo.com.au
      </p>
    </div>
  </section>
  <section class="card card-back" aria-label="Card back">
    <div class="brand"><span class="brand-dot"></span>Brisk Inquiries</div>
  </section>
</main>
</body>
</html>
```